Double Sided Flyer for 3D printing services company

We need a nice balanced flyer for our corporate handout. The attached is for concept only and not the final design. We think the attached examples have elements that balance nicely but the graphics are not good. We are attaching the logo from the corporate office for our new logo. We will add the company information after the final design is selected for web address, phone, mailing etc. Please leave room for that information in the design. Please ask any questions prior to submission. Our main focus is printing RUBBER 3D Parts and not plastic parts. The images selected should be focused on that. We also need to ensure the images are approved for use in a corporate flyer for content.

```html
<!DOCTYPE html>
<html lang="en">
<head>
<meta charset="utf-8">
<title>Kestrel Double Sided Flyer</title>
<link href="https://fonts.googleapis.com/css2?family=Poppins:wght@400;500;600;700;800&display=swap" rel="stylesheet">
<style>
:root{
  --orange:#e8541f;
  --orange-light:#f07a2a;
  --ink:#2b2b2b;
  --grey:#4a4a4a;
  --ring:#7d7d7d;
  --panel:#262626;
  --page:#ffffff;
  --stage:#f4f4f4;
}
*{box-sizing:border-box;margin:0;padding:0}
html,body{width:763px;height:1200px;overflow:hidden;background:var(--stage);font-family:'Poppins',sans-serif;color:var(--ink)}
.sheet{position:absolute;top:377px;width:315px;height:445px;background:var(--page);overflow:hidden;box-shadow:0 4px 12px rgba(0,0,0,.18)}
.sheet--front{left:56px}
.sheet--back{left:392px}
.abs{position:absolute}

/* brand */
.brand{right:13px;top:8px;display:flex;flex-direction:column;align-items:flex-end}
.brand__row{display:flex;align-items:center;gap:5px}
.brand__dot{width:15px;height:15px;border-radius:50%;background:var(--orange)}
.brand__name{font-weight:800;font-size:17px;color:var(--grey);letter-spacing:.5px;line-height:1}
.brand__tag{font-size:5.5px;font-weight:600;letter-spacing:.8px;color:var(--grey);margin-top:2px}

/* front headline */
.headline{left:15px;top:251px;line-height:1}
.headline__small{font-weight:800;font-size:20px;color:var(--grey);display:block;line-height:20px}
.headline__mid{font-weight:800;font-size:17.5px;color:var(--grey);display:block;line-height:21px}
.headline__big{font-weight:800;font-size:28.5px;color:var(--orange);display:block;line-height:27px;letter-spacing:-.2px}
.tagbar{left:15px;top:340px;width:288px;height:14px;background:var(--ink);border-radius:2px;color:#fff;font-size:8.6px;font-weight:600;letter-spacing:.9px;text-align:center;line-height:14px}

.perks{left:15px;top:361px;width:288px;display:flex;justify-content:space-between}
.perk{width:70px;text-align:center;font-size:6.3px;font-weight:700;line-height:7.5px;color:var(--ink);position:relative}
.perk svg{display:block;margin:0 auto 3px}
.perk + .perk::before{content:"›";position:absolute;left:-6px;top:20px;color:var(--orange);font-size:13px;font-weight:400}

.rule{left:15px;width:288px;height:1px;background:var(--orange-light)}
.contacts{left:15px;width:288px;display:flex;justify-content:space-between;font-size:7.6px;font-weight:700;line-height:10px}
.contact{display:flex;align-items:center;gap:3px;white-space:nowrap}
.contact__icon{width:8px;height:8px;border-radius:50%;background:var(--orange);display:inline-block;flex:none}

/* back */
.proto__title{left:14px;top:11px;font-weight:800;font-size:12.5px;line-height:12.5px;color:var(--orange)}
.proto__lead{left:14px;top:40px;font-weight:600;font-size:9px;line-height:10.5px;color:var(--grey)}
.proto__ask{left:14px;top:65px;font-size:6.6px;line-height:8px}
.proto__ask b{font-weight:700}
.steps{left:0;top:93px;width:315px;height:45px;background:var(--orange);color:#fff;padding:3px 0 0 14px}
.steps__title{font-weight:700;font-size:7.5px;letter-spacing:1px;line-height:11px}
.steps__list{list-style:none;font-size:6.2px;line-height:8.5px}
.confirm{left:15px;top:142px;font-size:6.2px;font-weight:700;letter-spacing:.1px;color:var(--grey)}

.products{left:20px;top:158px;width:275px;display:flex;justify-content:space-between}
.product{width:76px;text-align:center}
.product__pic{width:76px;height:76px;border-radius:50%;border:2.5px solid var(--orange);padding:3px;background:#fff}
.product__fill{width:100%;height:100%;border-radius:50%}
.product__fill--seal{background:radial-gradient(circle at 45% 45%,#d9535f,#a82a36 70%,#f2eeee 72%)}
.product__fill--gasket{background:radial-gradient(circle at 50% 55%,#f4f4f4 30%,#c9653f 32%,#8e3b25 45%,#2e2e2e 55%,#ececec 70%)}
.product__fill--hose{background:radial-gradient(circle at 50% 50%,#cfcfcf,#8b8b8b 55%,#f2f2f2 72%)}
.product__label{font-size:8.2px;font-weight:700;color:var(--grey);margin-top:3px;letter-spacing:.3px}

.benefits{left:15px;top:265px;width:287px;height:135px;background:var(--panel);border-radius:6px;border:1px solid var(--orange)}
.benefits__tab{left:60px;top:258px;width:199px;height:14px;background:var(--orange);color:#fff;font-weight:700;font-size:10px;letter-spacing:1.2px;text-align:center;line-height:14px}
.benefit-grid{left:20px;top:279px;width:277px;height:112px}
.cell{position:absolute;width:38px;height:37px;border:1px dashed var(--orange);border-radius:3px;color:#fff;padding:3px}
.cell__label{font-size:4.6px;font-weight:700;line-height:5.4px;margin-top:9px}
.cell__copy{font-size:3.4px;line-height:4.2px;color:#ddd}
.node{position:absolute;width:17px;height:17px;border-radius:50%;background:#fff;border:1.5px solid var(--orange)}
.node::after{content:"";position:absolute;left:4px;top:4px;width:6px;height:6px;border:1px solid var(--orange);border-radius:50%}
</style>
</head>
<body>

<!-- FRONT SIDE -->
<section class="sheet sheet--front">
  <svg class="abs" style="left:0;top:0" width="315" height="250" viewBox="0 0 315 250" role="img" aria-label="Photo of brass fittings, braided hoses and rubber gaskets inside a flange ring frame">
    <defs>
      <linearGradient id="frontPhoto" x1="0" y1="0" x2="1" y2="1">
        <stop offset="0" stop-color="#e9e9e9"/>
        <stop offset=".45" stop-color="#c9a456"/>
        <stop offset=".75" stop-color="#9a9a9a"/>
        <stop offset="1" stop-color="#dcdcdc"/>
      </linearGradient>
    </defs>
    <g transform="translate(160 138) rotate(-12)">
      <ellipse rx="168" ry="106" fill="var(--ring)"/>
      <circle cx="80" cy="86" r="4.5" fill="#fff"/>
      <circle cx="0" cy="99" r="4.5" fill="#fff"/>
      <circle cx="-80" cy="86" r="4.5" fill="#fff"/>
      <circle cx="-139" cy="50" r="4.5" fill="#fff"/>
      <circle cx="-160" cy="0" r="4.5" fill="#fff"/>
      <circle cx="-139" cy="-50" r="4.5" fill="#fff"/>
      <circle cx="139" cy="50" r="4.5" fill="#fff"/>
    </g>
    <ellipse cx="166" cy="132" rx="150" ry="92" transform="rotate(-12 166 132)" fill="#fff"/>
    <ellipse cx="170" cy="128" rx="140" ry="84" transform="rotate(-12 170 128)" fill="var(--orange)"/>
    <ellipse cx="162" cy="136" rx="126" ry="76" transform="rotate(-12 162 136)" fill="url(#frontPhoto)"/>
  </svg>

  <div class="abs brand">
    <div class="brand__row"><span class="brand__dot"></span><span class="brand__name">KESTREL</span></div>
    <span class="brand__tag">SEALS·GASKETS·HOSES</span>
  </div>

  <h1 class="abs headline">
    <span class="headline__small">YOUR</span>
    <span class="headline__small">TRUSTED</span>
    <span class="headline__mid">SOURCE FOR PREMIUM</span>
    <span class="headline__big">SEALING PRODUCTS</span>
  </h1>
  <div class="abs tagbar">APPLICATION EXPERTISE AND CUSTOM FABRICATION</div>

  <div class="abs perks">
    <div class="perk">
      <svg width="22" height="20" viewBox="0 0 22 20"><circle cx="11" cy="10" r="8" fill="none" stroke="var(--grey)" stroke-width="1.2"/><path d="M11 5v5l3 2" stroke="var(--orange)" stroke-width="1.3" fill="none"/></svg>
      Reduce Time to Market from Weeks to Hours
    </div>
    <div class="perk">
      <svg width="22" height="20" viewBox="0 0 22 20"><circle cx="11" cy="10" r="8" fill="none" stroke="var(--grey)" stroke-width="1.2"/><path d="M11 4v12M8 13l3 3 3-3" stroke="var(--orange)" stroke-width="1.3" fill="none"/></svg>
      Eliminate Costly Design Errors
    </div>
    <div class="perk">
      <svg width="22" height="20" viewBox="0 0 22 20"><circle cx="11" cy="10" r="8" fill="none" stroke="var(--grey)" stroke-width="1.2"/><path d="M7 14l8-8M10 6h5v5" stroke="var(--orange)" stroke-width="1.3" fill="none"/></svg>
      Faster Time to Market
    </div>
    <div class="perk">
      <svg width="22" height="20" viewBox="0 0 22 20"><circle cx="11" cy="10" r="8" fill="none" stroke="var(--grey)" stroke-width="1.2"/><circle cx="11" cy="10" r="4" fill="none" stroke="var(--orange)" stroke-width="1.3"/></svg>
      Reduced R and D Budgets
    </div>
  </div>

  <div class="abs rule" style="top:413px"></div>
  <div class="abs contacts" style="top:424px">
    <span class="contact"><span class="contact__icon"></span>555.010.4821</span>
    <span class="contact"><span class="contact__icon"></span>sales@kestrelseal.com</span>
    <span class="contact"><span class="contact__icon"></span>www.kestrelseal.com</span>
  </div>
</section>

<!-- BACK SIDE -->
<section class="sheet sheet--back">
  <div class="abs steps">
    <p class="steps__title">EASY AS 1 2 3</p>
    <ol class="steps__list">
      <li>1. Send us your Rubber part design file</li>
      <li>2. Recieve your estimate within 24 hours</li>
      <li>3. Receive your prototype sample within 10 days</li>
    </ol>
  </div>

  <svg class="abs" style="left:138px;top:0" width="177" height="132" viewBox="0 0 195 145" role="img" aria-label="Photo of braided steel hoses with brass fittings inside a flange ring frame">
    <defs>
      <linearGradient id="backPhoto" x1="0" y1="0" x2="1" y2="1">
        <stop offset="0" stop-color="#efefef"/>
        <stop offset=".5" stop-color="#b8b8b8"/>
        <stop offset=".7" stop-color="#c99a4a"/>
        <stop offset="1" stop-color="#e4e4e4"/>
      </linearGradient>
    </defs>
    <g transform="translate(110 70) rotate(-10)">
      <ellipse rx="100" ry="70" fill="var(--ring)"/>
      <circle cx="-92" cy="-15" r="3.5" fill="#fff"/>
      <circle cx="-86" cy="26" r="3.5" fill="#fff"/>
      <circle cx="-55" cy="57" r="3.5" fill="#fff"/>
      <circle cx="-5" cy="66" r="3.5" fill="#fff"/>
      <circle cx="48" cy="58" r="3.5" fill="#fff"/>
      <circle cx="88" cy="28" r="3.5" fill="#fff"/>
    </g>
    <ellipse cx="116" cy="66" rx="88" ry="60" transform="rotate(-10 116 66)" fill="#fff"/>
    <ellipse cx="118" cy="64" rx="82" ry="55" transform="rotate(-10 118 64)" fill="var(--orange)"/>
    <ellipse cx="116" cy="68" rx="75" ry="50" transform="rotate(-8 116 68)" fill="url(#backPhoto)"/>
  </svg>

  <h2 class="abs proto__title">QUICK<br>PROTOTYPING</h2>
  <p class="abs proto__lead">Redefine your<br>industry with 3D printing</p>
  <p class="abs proto__ask"><b>Need quality parts?</b><br>Let us print your custom one-off<br>or production pieces</p>

  <p class="abs confirm">CONFIRM FITMENT AND FUNCTION BEFORE LOSING TIME AND MONEY ON COSTLY MOLD</p>

  <div class="abs products">
    <div class="product">
      <div class="product__pic"><div class="product__fill product__fill--seal" role="img" aria-label="Photo of a red rubber seal"></div></div>
      <p class="product__label">SEALS</p>
    </div>
    <div class="product">
      <div class="product__pic"><div class="product__fill product__fill--gasket" role="img" aria-label="Photo of rubber gasket rings"></div></div>
      <p class="product__label">GASKETS</p>
    </div>
    <div class="product">
      <div class="product__pic"><div class="product__fill product__fill--hose" role="img" aria-label="Photo of a coiled braided hose"></div></div>
      <p class="product__label">HOSES</p>
    </div>
  </div>

  <div class="abs benefits"></div>
  <div class="abs benefits__tab">BENEFITS OF 3D PRINTING</div>
  <div class="abs benefit-grid">
    <div class="cell" style="left:18px;top:0"><p class="cell__label">SPEED<br>TIME TO<br>MARKET</p></div>
    <div class="cell" style="left:72px;top:0"><p class="cell__copy">Print small batches on demand without paying for costly tooling runs.</p></div>
    <div class="cell" style="left:126px;top:0"><p class="cell__label">WIN<br>BUSINESS</p></div>
    <div class="cell" style="left:180px;top:0"><p class="cell__copy">Iterate on new ideas freely and bring better parts to market.</p></div>
    <div class="cell" style="left:234px;top:0"><p class="cell__label">PERSONALISE<br>PRODUCTS</p></div>

    <div class="node" style="left:28px;top:47px"></div>
    <div class="node" style="left:82px;top:47px"></div>
    <div class="node" style="left:136px;top:47px"></div>
    <div class="node" style="left:190px;top:47px"></div>
    <div class="node" style="left:244px;top:47px"></div>

    <div class="cell" style="left:18px;top:73px"><p class="cell__copy">Test shapes fast, adjust early and move to production with confidence.</p></div>
    <div class="cell" style="left:72px;top:73px"><p class="cell__label">REDUCE<br>DEVELOPMENT<br>COST</p></div>
    <div class="cell" style="left:126px;top:73px"><p class="cell__copy">Show clients working rubber parts early and close deals sooner.</p></div>
    <div class="cell" style="left:180px;top:73px"><p class="cell__label">INCREASE<br>INNOVATION</p></div>
    <div class="cell" style="left:234px;top:73px"><p class="cell__copy">Tailor every seal, gasket and hose to the exact application.</p></div>
  </div>

  <div class="abs rule" style="top:413px"></div>
  <div class="abs contacts" style="top:424px">
    <span class="contact"><span class="contact__icon"></span>555.010.4821</span>
    <span class="contact"><span class="contact__icon"></span>sales@kestrelseal.com</span>
    <span class="contact"><span class="contact__icon"></span>www.kestrelseal.com</span>
  </div>
</section>

</body>
</html>
```